Valdane Companies Business Card Design

We need a new business card for our Private Equity Real Estate Development firm, “Valdane” and our EB-5 regional center “Thornmere Regional Center” on one card. We prefer a design that is simple, elegant, and represents the luxury products we design and build as well as the financial security and stability our successful history has produced. We are an industry leader in our field and 3rd generation family business that has evolved into an institutional quality investment platform. Considered design size is standard business card dimensions (3.5 x 2 inches with an additional 1/8 inch space for design elements or backgrounds that extend beyond the finished size of your piece.

Target Market(s)

• High net worth individuals
• Highly skilled technical workers and physicians in the US seeking investment-based immigration opportunities
• Sophisticated private equity investors
• Intermediary partners include domestic attorneys and investment brokers, as well as international agent networks
• US real estate developers

Industry/Entity Type

Finance

Contact Information for Business Card

(Providing placeholder info for personal information, please design for longer character spaces, longer names and addresses etc..)
• Logo for Valdane
• Logo for Thornmere Regional Center
• Full name: Marcus Valdane
• Job title: CEO
• Email address: mvaldane@valdanecompanies.com
• Cell phone number: +1.555.314.2287
• Office number +1.555.628.4410
• Office address: Larkfield Court 5, 4817 Vista Orilla, San Ramon, CA.
• Website: www.valdanecompanies.com

Font styles to use
Serif
Sans Serif

Colors
ec1f27
ffffff
000000

Requirements
Must have
• • Logo for Valdane
• • Logo for Thornmere Regional Center
• - Use rounded corners
• (See .ai file included for logos)
Nice to have
• • Simple, elegant design
• • Aesthetically compatible with our website design (www.valdanecompanies.com)
• • Color palette including but not limited to white, black, and red (as per logos)
Should not have
• - Not too much red color
• - Do not stack both logos on top of each other

```html
<!DOCTYPE html>
<html lang="en">
<head>
<meta charset="utf-8">
<title>Valdane Companies Business Card</title>
<link href="https://fonts.googleapis.com/css2?family=Tinos:wght@400;700&display=swap" rel="stylesheet">
<style>
  :root {
    --backdrop: #2b2b2d;
    --slate: #4a5a6b;
    --slate-map: #55677a;
    --paper: #ffffff;
    --crimson: #9b1b2e;
    --ink: #3a4250;
    --rule: #4a5565;
    --silver: #e9ecef;
  }
  * { margin: 0; padding: 0; box-sizing: border-box; }
  html, body {
    width: 1200px; height: 880px; overflow: hidden;
    background: var(--backdrop);
    font-family: "Tinos", "Times New Roman", serif;
  }
  .canvas { position: relative; width: 1200px; height: 880px; }

  .card {
    position: absolute; width: 560px; height: 320px;
    border-radius: 22px; overflow: hidden;
  }

  /* Front */
  .card--front { left: 80px; top: 80px; background: var(--slate); }
  .world-map {
    position: absolute; left: 90px; top: 40px; width: 400px; height: 200px;
    border-radius: 40px;
    background: radial-gradient(ellipse at center, var(--slate-map) 0%, var(--slate) 75%);
  }
  .front-brand {
    position: absolute; left: 0; right: 0; top: 120px;
    display: flex; align-items: center; justify-content: center; gap: 14px;
  }
  .brand-mark { width: 22px; height: 22px; background: var(--silver); }
  .front-brand .brand-name {
    color: var(--silver); font-size: 30px; font-weight: 700; letter-spacing: 1px;
  }
  .front-url {
    position: absolute; left: 0; right: 0; top: 238px; text-align: center;
    color: var(--paper); font-size: 13px; letter-spacing: 3px; text-transform: uppercase;
  }
  .front-url span { text-transform: lowercase; }

  /* Back */
  .card--back { left: 560px; top: 480px; background: var(--paper); }
  .back-brand {
    position: absolute; left: 36px; top: 70px;
    display: flex; align-items: center; gap: 12px;
  }
  .back-brand .brand-mark { background: var(--crimson); width: 20px; height: 20px; }
  .back-brand .brand-name { color: var(--crimson); font-size: 26px; font-weight: 700; letter-spacing: 1px; }
  .divider {
    position: absolute; left: 250px; right: 30px; top: 148px;
    border-top: 1px solid var(--rule);
  }
  .office-address {
    position: absolute; right: 30px; top: 160px; text-align: right;
    color: var(--ink); font-size: 14px; line-height: 1.25;
  }
  .person { position: absolute; left: 36px; top: 196px; }
  .person-name { color: var(--crimson); font-size: 22px; font-weight: 700; }
  .person-title { color: var(--ink); font-size: 14px; margin-bottom: 8px; }
  .contact-list { list-style: none; color: var(--ink); font-size: 14px; line-height: 1.35; }
  .contact-list li { display: flex; align-items: center; gap: 8px; }
  .contact-list svg { width: 12px; height: 12px; flex: none; }
</style>
</head>
<body>
<main class="canvas">
  <section class="card card--front">
    <div class="world-map" role="img" aria-label="Faint world map backdrop"></div>
    <div class="front-brand">
      <span class="brand-mark"></span>
      <span class="brand-name">THORNMERE REGIONAL CENTER</span>
    </div>
    <p class="front-url"><span>www.</span>valdanecompanies<span>.com</span></p>
  </section>

  <section class="card card--back">
    <div class="back-brand">
      <span class="brand-mark"></span>
      <span class="brand-name">THORNMERE REGIONAL CENTER</span>
    </div>
    <div class="divider"></div>
    <address class="office-address" style="font-style:normal">
      Larkfield Court 5<br>4817 Vista Orilla<br>San Ramon, CA.
    </address>
    <div class="person">
      <p class="person-name">Marcus Valdane</p>
      <p class="person-title">CEO</p>
      <ul class="contact-list">
        <li>
          <svg viewBox="0 0 12 12"><rect x="2" y="1" width="8" height="10" rx="1" fill="none" stroke="var(--crimson)" stroke-width="1.4"/></svg>
          +1.555.314.2287
        </li>
        <li>
          <svg viewBox="0 0 12 12"><path d="M1 5 Q6 0 11 5 L9 6 L8 4.5 L4 4.5 L3 6 Z M3 7 H9 V11 H3 Z" fill="var(--crimson)"/></svg>
          +1.555.628.4410
        </li>
        <li>
          <svg viewBox="0 0 12 12"><rect x="1" y="3" width="10" height="7" fill="var(--crimson)"/><path d="M1 3 L6 7 L11 3" fill="none" stroke="#fff" stroke-width="1"/></svg>
          mvaldane@valdanecompanies.com
        </li>
      </ul>
    </div>
  </section>
</main>
</body>
</html>
```